Lanternfield Drinks business cards

We need a business card design for our new logo. The company is modern, progressive, professional, yet approachable. The key products are ready to drink bottles and cans of coffee based beverages.
These cards will be a critical part of the first impression made by our sales organization, business development team, and all external facing personnel.
Card can be a vertical or horizontal orientation.

Target Market(s)

Customers, suppliers, business partners

Industry/Entity Type

Business

Contact Information for Business Card

Business cards should feature Company Name and Logo.

Font styles to use
Serif

Colors

Designer to choose colors to be used in the design.

Requirements
Must have
• Strong readability of Name, phone #, mobile number and email address.
• Job title, website url, Street Address, and other details can be secondary level readability.
Nice to have
• High impact, simplistic quality design.
• Ok to utilize the 'H in the box' separate from the company name

```html
<!DOCTYPE html>
<html lang="en">
<head>
<meta charset="utf-8">
<title>Lanternfield Drinks business cards</title>
<link href="https://fonts.googleapis.com/css2?family=Crimson+Text:wght@400;600;700&display=swap" rel="stylesheet">
<style>
  :root {
    --page-bg: #c9c9c9;
    --orange-top: #e2893a;
    --orange-bottom: #c9502c;
    --brand-red: #d4502e;
    --swoosh-orange: #e8922c;
    --card-white: #f7f7f5;
    --ink: #2a2a2a;
    --white: #ffffff;
  }
  * { margin: 0; padding: 0; box-sizing: border-box; }
  html, body { width: 1200px; height: 576px; overflow: hidden; }
  body {
    background: var(--page-bg);
    position: relative;
    font-family: "Crimson Text", Georgia, serif;
  }
  .card {
    position: absolute;
    top: 138px;
    width: 484px;
    height: 294px;
    border-radius: 14px;
    overflow: hidden;
  }
  /* Front */
  .card-front {
    left: 82px;
    background: linear-gradient(180deg, var(--orange-top), var(--orange-bottom));
  }
  .card-front .brand-square {
    position: absolute;
    left: 204px;
    top: 78px;
    width: 76px;
    height: 76px;
    border: 3px solid var(--white);
  }
  .card-front .brand-name {
    position: absolute;
    left: 0;
    right: 0;
    top: 164px;
    text-align: center;
    color: var(--white);
    font-weight: 700;
    font-size: 29px;
    line-height: 36px;
    letter-spacing: 0.5px;
    white-space: nowrap;
  }
  /* Back */
  .card-back {
    left: 602px;
    width: 482px;
    height: 292px;
    background: var(--card-white);
  }
  .card-back .wave { position: absolute; inset: 0; }
  .person {
    position: absolute;
    right: 25px;
    top: 20px;
    text-align: right;
    color: var(--white);
  }
  .person-name { font-size: 20px; font-weight: 700; line-height: 24px; }
  .person-title { font-size: 12.5px; line-height: 16px; margin-top: 4px; }
  .card-back .brand-square {
    position: absolute;
    left: 108px;
    top: 74px;
    width: 68px;
    height: 68px;
    border: 3px solid var(--brand-red);
  }
  .card-back .brand-name {
    position: absolute;
    left: 18px;
    width: 248px;
    top: 150px;
    text-align: center;
    color: var(--brand-red);
    font-weight: 700;
    font-size: 26px;
    line-height: 34px;
    white-space: nowrap;
  }
  .address {
    position: absolute;
    left: 24px;
    top: 228px;
    font-size: 13px;
    line-height: 18px;
    color: var(--ink);
  }
  .contact {
    position: absolute;
    right: 26px;
    top: 200px;
    list-style: none;
    font-size: 13px;
    line-height: 17px;
    color: var(--ink);
  }
  .contact li {
    display: flex;
    justify-content: flex-end;
    align-items: center;
    gap: 8px;
  }
  .contact svg { width: 10px; height: 10px; fill: var(--brand-red); flex: none; }
</style>
</head>
<body>
  <section class="card card-front" aria-label="Card front">
    <div class="brand-square"></div>
    <div class="brand-name">Lanternfield Drinks</div>
  </section>

  <section class="card card-back" aria-label="Card back">
    <svg class="wave" viewBox="0 0 482 292" preserveAspectRatio="none" aria-hidden="true">
      <path fill="var(--brand-red)" d="M0,0 H482 V118 C420,122 360,84 300,58 C230,30 120,14 0,26 Z"/>
      <path fill="var(--swoosh-orange)" d="M0,60 C90,22 200,26 290,62 C360,92 420,128 482,132 V140 C410,136 350,104 280,74 C190,38 90,34 0,70 Z"/>
      <path fill="var(--swoosh-orange)" d="M40,58 C130,26 230,32 300,62 C240,42 140,36 40,58 Z"/>
    </svg>
    <div class="person">
      <div class="person-name">Marlo Quentin Reyes</div>
      <div class="person-title">Managing Director</div>
    </div>
    <div class="brand-square"></div>
    <div class="brand-name">Lanternfield Drinks</div>
    <div class="address">418 Brookline Ave.,<br>Fairhaven, US 204118</div>
    <ul class="contact">
      <li>312.408.2261 <svg viewBox="0 0 10 10"><path d="M1 3 Q5 0 9 3 L8 5 L6 4 L4 4 L2 5 Z M2 6 H8 V9 H2 Z"/></svg></li>
      <li>312.977.5043 <svg viewBox="0 0 10 10"><path d="M3 0 H7 Q8 0 8 1 V9 Q8 10 7 10 H3 Q2 10 2 9 V1 Q2 0 3 0 Z M3 1.5 V7.5 H7 V1.5 Z"/></svg></li>
      <li>mreyes@lanternfield.com <svg viewBox="0 0 10 10"><path d="M0 2 H10 V8 H0 Z M0.8 2.6 L5 5.6 L9.2 2.6 V3.4 L5 6.4 L0.8 3.4 Z" fill-rule="evenodd"/></svg></li>
      <li>www.lanternfield.com <svg viewBox="0 0 10 10"><circle cx="5" cy="5" r="4.5"/></svg></li>
    </ul>
  </section>
</body>
</html>
```